Corvana Tongue Works, LLC

We need a business card that includes information about our business and conveys a reliable business that provides document translation services and interpreters for a variety of corporate and individual clients. We want to come across as professional, reliable, yet approachable. It should include the following on one side:

ESL / ENL Language Classes, Private Lessons, and Online Tutors
PLEXA Training and Testing
Translating & Interpreting Services
Contact us about Over-the-Phone Interpreting in over 200 languages
24/7/365
www.corvanatongue.example

The other side should include (555) 481-3062

Rhoda Pelling, President
482 Garnet Ave., Ste. 219
Indianapolis, IN 40917

Please add USA as part of the address. Also, please add rmpelling@corvanatongueworks.example as the e-mail address. Thank you.

Target Market(s)

Business professionals, their families, the international community

Industry/Entity Type

Business

Contact Information for Business Card

24/7/365
www.corvanatongue.example

(555) 481-3062

Rhoda Pelling, President
482 Garnet Ave., Ste. 219
Indianapolis, IN 40917
USA

Font styles to use
Sans Serif

Colors

Designer to choose colors to be used in the design.

Requirements
Must have
• See project description
• e-mail address and web address
• Phone number
Nice to have
• a globe
• physical address
Should not have
• Should not have the same color scheme as other agencies in our market in Indiana unless it is blue and black. No purple or yellow.

```html
<!DOCTYPE html>
<html lang="en">
<head>
<meta charset="utf-8">
<title>Corvana Tongue Works — Business Card</title>
<link href="https://fonts.googleapis.com/css2?family=Arimo:wght@400;700&display=swap" rel="stylesheet">
<style>
  :root {
    --brand-blue: #2596d4;
    --ink: #111111;
    --paper: #ffffff;
    --backdrop: #262626;
    --tint: #eef4fb;
    --map-tone: #f1f2f3;
  }
  * { box-sizing: border-box; margin: 0; padding: 0; }
  html, body { width: 1189px; height: 1200px; overflow: hidden; }
  body {
    background: var(--backdrop);
    font-family: "Arimo", Arial, sans-serif;
    color: var(--ink);
    position: relative;
  }
  .card {
    position: absolute;
    left: 167px;
    width: 855px;
    height: 488px;
    background: var(--paper);
    border-radius: 40px;
    overflow: hidden;
  }
  .card--front { top: 67px; }
  .card--back { top: 625px; }

  /* Front */
  .world-map {
    position: absolute;
    left: 80px; top: 80px; width: 700px; height: 340px;
    background: radial-gradient(ellipse at center, var(--map-tone) 0%, rgba(241,242,243,0.4) 60%, rgba(255,255,255,0) 80%);
  }
  .brand {
    position: absolute;
    display: flex; align-items: center; gap: 12px;
  }
  .brand__mark {
    border-radius: 50%;
    background: var(--brand-blue);
    flex: none;
  }
  .brand__name {
    font-weight: 700;
    color: var(--ink);
    line-height: 1.12;
  }
  .card--front .brand { left: 253px; top: 87px; }
  .card--front .brand__mark { width: 150px; height: 150px; border: 6px solid var(--paper); box-shadow: 0 0 0 3px var(--brand-blue); }
  .card--front .brand__name { font-size: 38px; }

  .services {
    position: absolute; left: 0; right: 0; top: 275px;
    text-align: center; font-size: 21px; line-height: 27px;
  }
  .website {
    position: absolute; left: 0; right: 0; top: 375px;
    text-align: center; font-size: 21px; letter-spacing: 4px;
  }
  .website .accent { color: var(--brand-blue); }
  .contact-band {
    position: absolute; left: 0; right: 0; top: 419px; height: 45px;
    background: var(--brand-blue); color: var(--paper);
    font-size: 19.5px; text-align: center; line-height: 45px;
  }

  /* Back */
  .side-band {
    position: absolute; left: 0; top: 0; bottom: 0; width: 108px;
    background: var(--brand-blue);
  }
  .side-rule {
    position: absolute; left: 112px; top: 0; bottom: 0; width: 7px;
    background: var(--brand-blue);
  }
  .watermark-circle {
    position: absolute; left: 440px; top: -110px; width: 490px; height: 490px;
    border-radius: 50%; background: var(--tint);
    border: 12px solid #f6f9fd;
  }
  .card--back .brand { left: 47px; top: 48px; }
  .card--back .brand__mark { width: 156px; height: 156px; border: 8px solid var(--paper); box-shadow: 0 0 0 3px var(--brand-blue); }
  .card--back .brand__name { font-size: 36px; margin-left: 4px; }

  .person { position: absolute; left: 216px; top: 256px; }
  .person__name { font-size: 30px; font-weight: 700; letter-spacing: -0.5px; line-height: 34px; }
  .person__title { font-size: 21px; color: var(--brand-blue); line-height: 22px; }

  .contacts { position: absolute; left: 216px; top: 328px; list-style: none; }
  .contacts li {
    display: flex; align-items: center; gap: 10px;
    font-size: 21px; height: 31px;
  }
  .contacts svg { width: 28px; height: 28px; flex: none; }
</style>
</head>
<body>

<section class="card card--front" aria-label="Card front">
  <div class="world-map" role="img" aria-label="Faint world map in the background"></div>
  <div class="brand">
    <span class="brand__mark"></span>
    <span class="brand__name">Corvana<br>Tongue<br>Works, LLC</span>
  </div>
  <p class="services">
    ESL / ENL Language Classes | Private Lessons and Online Tutors<br>
    PLEXA Training and Testing<br>
    Translating &amp; Interpreting Services
  </p>
  <p class="website">www.<span class="accent">corvanatongue</span>.example</p>
  <p class="contact-band">Contact us about Over-the-Phone Interpreting in over 200 languages 24/7/365</p>
</section>

<section class="card card--back" aria-label="Card back">
  <div class="watermark-circle"></div>
  <div class="side-band"></div>
  <div class="side-rule"></div>
  <div class="brand">
    <span class="brand__mark"></span>
    <span class="brand__name">Corvana<br>Tongue<br>Works, LLC</span>
  </div>
  <div class="person">
    <p class="person__name">Rhoda Pelling</p>
    <p class="person__title">President</p>
  </div>
  <ul class="contacts">
    <li>
      <svg viewBox="0 0 28 28" aria-hidden="true"><circle cx="14" cy="14" r="14" fill="var(--brand-blue)"/><path d="M7 12c0-3 14-3 14 0v2h-4v-2h-6v2H7z M9 15h10l1 5H8z" fill="#fff"/></svg>
      (555) 481-3062
    </li>
    <li>
      <svg viewBox="0 0 28 28" aria-hidden="true"><circle cx="14" cy="14" r="14" fill="var(--brand-blue)"/><rect x="7" y="9" width="14" height="10" fill="none" stroke="#fff" stroke-width="1.6"/><path d="M7 9l7 6 7-6" fill="none" stroke="#fff" stroke-width="1.6"/></svg>
      rmpelling@corvanatongueworks.example
    </li>
    <li>
      <svg viewBox="0 0 28 28" aria-hidden="true"><circle cx="14" cy="14" r="14" fill="var(--brand-blue)"/><g fill="none" stroke="#fff" stroke-width="1.4"><circle cx="14" cy="14" r="8"/><ellipse cx="14" cy="14" rx="3.5" ry="8"/><path d="M6 14h16M7.5 10h13M7.5 18h13"/></g></svg>
      www.corvanatongue.example
    </li>
    <li>
      <svg viewBox="0 0 28 28" aria-hidden="true"><circle cx="14" cy="14" r="14" fill="var(--brand-blue)"/><path d="M14 22s-6-6.5-6-10.5a6 6 0 0 1 12 0C20 15.5 14 22 14 22z" fill="none" stroke="#fff" stroke-width="1.6"/><circle cx="14" cy="11.5" r="2.2" fill="#fff"/></svg>
      482 Garnet Ave., Ste. 219, Indianapolis, IN 40917, USA
    </li>
  </ul>
</section>

</body>
</html>
```